Bright Wave Labs

We need a professional letter head format for our company. Now we have a logo but need to desing a new logo also. I have uploaded our old logo. Use the color in the logo and design a new one.

Dear Designers , Need to mention "BWL" and please dont use our old LOGO. we need a new catchy one.

```html
<!DOCTYPE html>
<html lang="en">
<head>
<meta charset="utf-8">
<title>Bright Wave Labs — Letterhead</title>
<link rel="stylesheet" href="https://fonts.googleapis.com/css2?family=Source+Sans+3:wght@400;600;700&family=Arimo:wght@700&display=swap">
<style>
  :root {
    --navy: #0c2238;
    --green: #8dc63f;
    --lime: #d9e021;
    --ink: #4a4a4a;
    --page: #ffffff;
    --backdrop: #e6e6e6;
  }
  * { box-sizing: border-box; margin: 0; padding: 0; }
  html, body {
    width: 1200px; height: 1200px; overflow: hidden;
    background: var(--backdrop);
  }
  .letterhead {
    position: absolute; left: 230px; top: 78px;
    width: 740px; height: 1044px;
    background: var(--page);
    box-shadow: 0 6px 24px rgba(0,0,0,0.12);
    font-family: "Source Sans 3", sans-serif;
    color: var(--ink);
  }
  .brand {
    position: absolute; top: 58px; left: 0; width: 100%;
    display: flex; flex-direction: column; align-items: center; gap: 18px;
  }
  .brand-dot {
    width: 56px; height: 56px; border-radius: 50%;
    background: var(--green);
  }
  .brand-name {
    font-size: 15px; font-weight: 700; letter-spacing: 0.5px;
    color: var(--navy); text-transform: uppercase;
  }
  .salutation {
    position: absolute; top: 250px; left: 57px;
    font-family: "Arimo", sans-serif; font-weight: 700; font-size: 16px;
    color: var(--ink);
  }
  .letter-body {
    position: absolute; top: 290px; left: 57px; width: 626px;
  }
  .letter-body p {
    font-size: 14.6px; line-height: 19.4px; text-align: justify;
    margin-bottom: 19px;
  }
  .signature {
    position: absolute; top: 718px; left: 58px;
    width: 138px; height: 70px;
    background: linear-gradient(90deg, #eeeeee, #f6f6f6);
    border-radius: 4px;
  }
  .footer {
    position: absolute; left: 0; bottom: 0; width: 740px; height: 90px;
  }
  .footer svg.band { position: absolute; left: 0; top: 0; }
  .footer-text {
    position: absolute; left: 0; width: 100%; top: 48px;
    text-align: center; color: #ffffff; font-size: 11px; line-height: 17px;
  }
  .contact-line { display: flex; justify-content: center; align-items: center; gap: 6px; font-size: 12px; }
  .contact-line svg { width: 10px; height: 10px; fill: #ffffff; }
</style>
</head>
<body>
  <div class="letterhead">
    <header class="brand">
      <span class="brand-dot"></span>
      <span class="brand-name">Bright Wave Labs</span>
    </header>

    <div class="salutation">Dear Mr. Harlan,</div>

    <main class="letter-body">
      <p>Lorem Ipsum is simply dummy text of the printing and typesetting industry. Lorem Ipsum has been the industry's standard dummy text ever since the 1500s, when an unknown printer took a galley of type and scrambled it to make a type specimen book. It has survived not only five centuries, but also the leap into electronic typesetting, remaining essentially unchanged.</p>
      <p>The standard chunk of Lorem Ipsum used since the 1500s is reproduced below for those interested. Sections 1.10.32 and 1.10.33 from "de Finibus Bonorum et Malorum" by Corvinus are also reproduced in their exact original form, accompanied by English versions from the 1914 translation by H. Marlow</p>
      <p>Lorem Ipsum is simply dummy text of the printing and typesetting industry. Lorem Ipsum has been the industry's standard dummy text ever since the 1500s, when an unknown printer took a galley of type and scrambled it to make a type specimen book. It has survived not only five centuries, but also the leap into electronic typesetting, remaining essentially unchanged. It was popularised in the</p>
      <p>Lorem Ipsum is simply dummy text of the printing and typesetting industry. Lorem Ipsum has been the industry's standard dummy text ever since the 1500s, when an unknown printer took a galley of type and scrambled it to make a type specimen book. It has survived not only five centuries, but also the leap into electronic typesetting, remaining essentially unchanged. It was popularised in the</p>
    </main>

    <div class="signature" role="img" aria-label="Handwritten signature of the sender"></div>

    <footer class="footer">
      <svg class="band" width="740" height="90" viewBox="0 0 740 90">
        <path d="M0 14 Q370 44 740 10 L740 90 L0 90 Z" fill="var(--navy)"/>
        <path d="M8 8 Q370 38 740 0" fill="none" stroke="var(--green)" stroke-width="3"/>
      </svg>
      <div class="footer-text">
        <div>Po. box 201, Street Name, City Name, Zip Code - 00000</div>
        <div class="contact-line">
          <svg viewBox="0 0 10 10"><path d="M2 0.5 L3.6 2.6 L2.8 3.6 Q4 6 6.4 7.2 L7.4 6.4 L9.5 8 L8.4 9.5 Q3.5 9 0.5 1.6 Z"/></svg>
          <span>(+961)472-318-204</span>
          <svg viewBox="0 0 10 10"><path d="M0.5 2 H9.5 V8.5 H0.5 Z M1.3 2.6 L5 5.6 L8.7 2.6" fill="none" stroke="#fff" stroke-width="1"/></svg>
          <span>info@brightwavelabs.com</span>
          <svg viewBox="0 0 10 10"><circle cx="5" cy="5" r="4.3" fill="none" stroke="#fff" stroke-width="1"/><path d="M0.7 5 H9.3 M5 0.7 Q2 5 5 9.3 M5 0.7 Q8 5 5 9.3" fill="none" stroke="#fff" stroke-width="0.8"/></svg>
          <span>www.brightwavelabs.com</span>
        </div>
      </div>
    </footer>
  </div>
</body>
</html>
```